Professional Package for CPA Firm

We would like a stationery design for our new CPA Firm based in Atlanta, GA called 'Vale 8'. We work with investors to help grow investments, tax free. We would like the design to have a professional/minimal look with a 'wow' factor. We need 9.5″ x 4.125″, 9x12, and 10x13 mailing envelopes, business cards, and a letterhead. We have a logo that is already complete. For the letterhead, we would like to have space to put credentials at the bottom of the page

Industry/Entity Type

CPA, Accounting

```html
<!DOCTYPE html>
<html lang="en">
<head>
<meta charset="utf-8">
<title>Vale 8 — Stationery Package</title>
<link rel="stylesheet" href="https://fonts.googleapis.com/css2?family=Montserrat:wght@300;400;500;700;800&family=Arimo:wght@400;700&display=swap">
<style>
  :root{
    --navy:#032d3c;
    --teal:#21a0b0;
    --red:#f2434b;
    --stage:#acacac;
    --paper:#ffffff;
    --paper-tint:#ececec;
    --ink-soft:#858b90;
    --ink-mid:#5c6368;
    --rule:#b9bcbe;
  }
  *{box-sizing:border-box;margin:0;padding:0}
  html,body{width:849px;height:1200px;overflow:hidden}
  body{background:var(--stage);position:relative;font-family:"Montserrat",sans-serif;color:var(--navy)}
  .sheet{position:absolute;background:var(--paper);box-shadow:1px 2px 4px rgba(0,0,0,.28);overflow:hidden}
  .sheet--tinted{background:linear-gradient(90deg,var(--paper-tint) 0%,var(--paper) 60%)}

  /* footer band: flat area in the piece's main tones */
  .footer-band{position:absolute;left:0;bottom:0;width:100%;
    background:linear-gradient(90deg,var(--navy) 0%,var(--navy) 55%,#0b4a5a 85%,var(--teal) 100%)}

  /* wordmark stand-in */
  .brand{display:flex;flex-direction:column;align-items:flex-start}
  .brand__row{display:flex;align-items:center}
  .brand__dot{border-radius:50%;background:var(--red);flex:none}
  .brand__name{font-family:"Montserrat",sans-serif;font-weight:800;color:var(--navy);line-height:1;letter-spacing:.02em}
  .brand__tag{font-family:"Montserrat",sans-serif;font-weight:500;color:var(--navy);line-height:1;white-space:nowrap}
  .brand--light .brand__name,.brand--light .brand__tag{color:#fff}
  .brand--light .brand__dot{background:var(--teal)}
  .return-address{font-family:"Arimo",sans-serif;color:var(--ink-mid);line-height:1.25}

  .icon{width:1em;height:1em;flex:none;fill:var(--red)}
  .contact-line{display:flex;align-items:center;gap:.45em;white-space:nowrap}

  /* business card front */
  .card-front{left:123px;top:32px;width:289px;height:165px}
  .card-front .brand{position:absolute;left:40px;top:58px}
  .card-front .brand__dot{width:12px;height:12px;margin-right:6px}
  .card-front .brand__name{font-size:25px}
  .card-front .brand__tag{font-size:7.6px;margin-top:6px}
  .card-front__divider{position:absolute;left:144px;top:38px;width:1px;height:90px;background:var(--rule)}
  .card-front__details{position:absolute;left:157px;top:38px;font-family:"Arimo",sans-serif;color:var(--ink-mid);font-size:7.9px;line-height:1.3}
  .card-front__name{color:var(--red);font-weight:700;font-size:9.7px;letter-spacing:.01em}
  .card-front__role{margin-bottom:8px}
  .card-front__address{margin-bottom:8px}
  .card-front__details .contact-line{margin-bottom:1.6px}
  .card-front .footer-band{height:14px}

  /* business card back */
  .card-back{left:452px;top:32px;width:289px;height:165px;background:var(--navy)}
  .card-back .brand{position:absolute;left:20px;top:88px}
  .card-back .brand__dot{width:13px;height:13px;margin-right:7px}
  .card-back .brand__name{font-size:27px}
  .card-back .brand__tag{font-size:8.4px;margin-top:6px}

  /* letterhead */
  .letterhead{left:37px;top:225px;width:379px;height:535px}
  .letterhead .brand{position:absolute;left:25px;top:36px}
  .letterhead .brand__dot{width:7px;height:7px;margin-right:4px}
  .letterhead .brand__name{font-size:14px}
  .letterhead .brand__tag{font-size:3.9px;margin-top:3px}
  .letterhead__contact{position:absolute;left:284px;top:18px;font-family:"Arimo",sans-serif;font-size:5.6px;line-height:1.3;color:var(--ink-mid)}
  .letterhead__contact .contact-line{margin-top:1.6px}
  .letterhead__contact address{font-style:normal;margin-bottom:3px}
  .letterhead__rule{position:absolute;left:25px;top:66px;width:328px;height:1px;background:var(--rule)}
  .letter__to{position:absolute;left:38px;top:119px;font-size:6.6px;letter-spacing:.15em;color:var(--navy)}
  .letter__date{position:absolute;right:39px;top:120px;font-size:5px;color:var(--ink-mid)}
  .letter__recipient{position:absolute;left:38px;top:131px;font-size:4.6px;line-height:1.8;color:var(--ink-soft);font-weight:400}
  .letter__recipient-name{color:var(--red);font-size:6.1px;font-weight:400;margin-bottom:1px}
  .letter__body{position:absolute;left:38px;top:193px;width:302px;font-size:4.75px;line-height:1.42;color:var(--ink-soft);font-weight:400;text-align:justify}
  .letter__body p{margin-bottom:6.6px}
  .letter__signature{position:absolute;left:37px;top:375px;width:64px;height:16px;border-radius:3px;background:linear-gradient(90deg,rgba(3,45,60,.14),rgba(3,45,60,.05))}
  .letter__signer{position:absolute;left:37px;top:398px;font-size:6px;color:var(--navy)}
  .letter__signer-role{display:block;font-size:4.4px;color:var(--ink-soft);font-weight:400;margin-top:2px}
  .letterhead .footer-band{height:20px}

  /* 10 x 13 envelope */
  .env-large{left:456px;top:225px;width:354px;height:460px}
  .env-large .brand{position:absolute;left:20px;top:52px}
  .env-large .brand__dot{width:8px;height:8px;margin-right:5px}
  .env-large .brand__name{font-size:17px}
  .env-large .brand__tag{font-size:5.1px;margin-top:3px}
  .env-large .return-address{position:absolute;left:21px;top:82px;font-size:5.1px}
  .env-large .footer-band{height:20px}

  /* 9 x 12 envelope */
  .env-medium{left:456px;top:730px;width:336px;height:424px}
  .env-medium .brand{position:absolute;left:18px;top:50px}
  .env-medium .brand__dot{width:8px;height:8px;margin-right:5px}
  .env-medium .brand__name{font-size:17px}
  .env-medium .brand__tag{font-size:5.1px;margin-top:3px}
  .env-medium .return-address{position:absolute;left:18px;top:80px;font-size:5.1px}
  .env-medium .footer-band{height:19px}

  /* #10 envelope front */
  .env-front{left:28px;top:794px;width:387px;height:168px}
  .env-front .brand{position:absolute;left:12px;top:38px}
  .env-front .brand__dot{width:6px;height:6px;margin-right:3px}
  .env-front .brand__name{font-size:11.5px}
  .env-front .brand__tag{font-size:3.4px;margin-top:2px}
  .env-front .return-address{position:absolute;left:12px;top:58px;font-size:5px}
  .env-front .footer-band{height:20px}

  /* #10 envelope back */
  .env-back{left:28px;top:987px;width:387px;height:168px}
  .env-back__flap{position:absolute;left:0;top:0;width:100%;height:52px;display:block}
  .env-back .brand{position:absolute;left:50%;top:20px;transform:translateX(-50%);align-items:center}
  .env-back .brand__dot{width:5px;height:5px;margin-right:3px}
  .env-back .brand__name{font-size:9.5px}
  .env-back .brand__tag{font-size:2.6px;margin-top:2px}
</style>
</head>
<body>

<svg width="0" height="0" style="position:absolute" aria-hidden="true">
  <defs>
    <symbol id="icon-phone" viewBox="0 0 16 16">
      <path d="M4.2 1.5l2.2 2.7-1.3 1.6c.8 1.9 2.3 3.4 4.2 4.2l1.6-1.3 2.7 2.2-1.3 2.4c-5.2-.2-9.6-4.6-9.8-9.8z"/>
    </symbol>
    <symbol id="icon-mail" viewBox="0 0 16 16">
      <path d="M1.5 3.5h13v9h-13z M2.5 4.5l5.5 4.2 5.5-4.2" fill="none" stroke="#f2434b" stroke-width="1.6"/>
    </symbol>
    <symbol id="icon-globe" viewBox="0 0 16 16">
      <circle cx="8" cy="8" r="6.5" fill="none" stroke="#f2434b" stroke-width="1.5"/>
      <path d="M1.5 8h13 M8 1.5c-3 3.5-3 9.5 0 13 M8 1.5c3 3.5 3 9.5 0 13" fill="none" stroke="#f2434b" stroke-width="1.2"/>
    </symbol>
  </defs>
</svg>

<!-- Business card, front -->
<section class="sheet card-front" aria-label="Business card front">
  <div class="brand">
    <div class="brand__row"><span class="brand__dot"></span><span class="brand__name">VALE 8</span></div>
    <span class="brand__tag">CPAS and Tax Advisors</span>
  </div>
  <div class="card-front__divider"></div>
  <div class="card-front__details">
    <div class="card-front__name">DANIEL REYES</div>
    <div class="card-front__role">Manager</div>
    <div class="card-front__address">Your address, city<br>state, ZIP 0000</div>
    <div class="contact-line"><svg class="icon"><use href="#icon-phone"/></svg>404-555-0187</div>
    <div class="contact-line"><svg class="icon"><use href="#icon-mail"/></svg>hello@vale8cpa.com</div>
    <div class="contact-line"><svg class="icon"><use href="#icon-globe"/></svg>www.vale8cpa.com</div>
  </div>
  <div class="footer-band" role="img" aria-label="Decorative footer band in navy and teal"></div>
</section>

<!-- Business card, back -->
<section class="sheet card-back" aria-label="Business card back">
  <div class="brand brand--light">
    <div class="brand__row"><span class="brand__dot"></span><span class="brand__name">VALE 8</span></div>
    <span class="brand__tag">CPAS and Tax Advisors</span>
  </div>
</section>

<!-- Letterhead -->
<section class="sheet sheet--tinted letterhead" aria-label="Letterhead">
  <div class="brand">
    <div class="brand__row"><span class="brand__dot"></span><span class="brand__name">VALE 8</span></div>
    <span class="brand__tag">CPAS and Tax Advisors</span>
  </div>
  <div class="letterhead__contact">
    <address>Your address, city<br>state, ZIP 0000</address>
    <div class="contact-line"><svg class="icon"><use href="#icon-phone"/></svg>404-555-0187</div>
    <div class="contact-line"><svg class="icon"><use href="#icon-mail"/></svg>hello@vale8cpa.com</div>
    <div class="contact-line"><svg class="icon"><use href="#icon-globe"/></svg>www.vale8cpa.com</div>
  </div>
  <div class="letterhead__rule"></div>

  <div class="letter__to">TO</div>
  <div class="letter__date">Friday, 01/01/2018</div>
  <div class="letter__recipient">
    <div class="letter__recipient-name">Laura Penning</div>
    Human Resources<br>
    Northfield Co.<br>
    214 Brook Lane, Dalton<br>
    GA 30301
  </div>

  <div class="letter__body">
    <p>Thank you for meeting with our team last week. We have reviewed the portfolio summary you shared and prepared an outline of next steps. Our advisors will map each holding against current tax rules and flag accounts that could benefit from a change in structure before the next filing season begins.</p>
    <p>We will send a short checklist of documents this week. Most items can be shared through our secure client portal.</p>
    <p>Please keep copies of all recent statements on file.</p>
    <p>Once the review is complete, we will meet again to walk through our findings in plain terms. You will receive a written plan that sets out each recommendation, the expected effect on your tax position and a simple timeline.</p>
    <p>Our goal is to help your investments grow with as little tax drag as the law allows. We take a careful, steady approach and explain every step so that you stay in control of each decision. If anything in this letter is unclear, please reach out to our office at any time and we will be glad to help.</p>
    <p>We look forward to working with you in the months ahead.</p>
  </div>

  <div class="letter__signature" role="img" aria-label="Handwritten signature of Owen Hartley"></div>
  <div class="letter__signer">Owen Hartley<span class="letter__signer-role">Managing Director</span></div>

  <div class="footer-band" role="img" aria-label="Decorative footer band in navy and teal"></div>
</section>

<!-- 10 x 13 envelope -->
<section class="sheet sheet--tinted env-large" aria-label="10 by 13 mailing envelope">
  <div class="brand">
    <div class="brand__row"><span class="brand__dot"></span><span class="brand__name">VALE 8</span></div>
    <span class="brand__tag">CPAS and Tax Advisors</span>
  </div>
  <p class="return-address">Your address, city<br>state, ZIP 0000</p>
  <div class="footer-band" role="img" aria-label="Decorative footer band in navy and teal"></div>
</section>

<!-- 9 x 12 envelope -->
<section class="sheet sheet--tinted env-medium" aria-label="9 by 12 mailing envelope">
  <div class="brand">
    <div class="brand__row"><span class="brand__dot"></span><span class="brand__name">VALE 8</span></div>
    <span class="brand__tag">CPAS and Tax Advisors</span>
  </div>
  <p class="return-address">Your address, city<br>state, ZIP 0000</p>
  <div class="footer-band" role="img" aria-label="Decorative footer band in navy and teal"></div>
</section>

<!-- #10 envelope, front -->
<section class="sheet sheet--tinted env-front" aria-label="9.5 by 4.125 envelope front">
  <div class="brand">
    <div class="brand__row"><span class="brand__dot"></span><span class="brand__name">VALE 8</span></div>
    <span class="brand__tag">CPAS and Tax Advisors</span>
  </div>
  <p class="return-address">Your address, city<br>state, ZIP 0000</p>
  <div class="footer-band" role="img" aria-label="Decorative footer band in navy and teal"></div>
</section>

<!-- #10 envelope, back -->
<section class="sheet sheet--tinted env-back" aria-label="9.5 by 4.125 envelope back">
  <svg class="env-back__flap" viewBox="0 0 387 52" preserveAspectRatio="none" aria-hidden="true">
    <path d="M0,0 L387,0 L374,34 C370,44 362,47 352,47 L35,47 C25,47 17,44 13,34 Z" fill="#ffffff" stroke="#e2e2e2" stroke-width="1"/>
    <path d="M35,48 L352,48" stroke="rgba(0,0,0,.12)" stroke-width="2"/>
  </svg>
  <div class="brand">
    <div class="brand__row"><span class="brand__dot"></span><span class="brand__name">VALE 8</span></div>
    <span class="brand__tag">CPAS and Tax Advisors</span>
  </div>
</section>

</body>
</html>
```